Soy Candle Labels

We sell soy candles in recycled wine bottles. The wine bottle is cut in half and filled with pure and natural soy wax and scented with essential oils.
Our product represents good use of up cycling materials for a better use. The product is all natural and eco friendly.
You can see good use of labels and branding for a company in America that does the same thing http://larkmeadow7wicks.example/
Trya dn keep the label uncomplicated like the above labels.
We will need an area to hand stamp the scent. Similar to the labels used on the above website.
We would prefer to use a white or off white paper label with gold or bronze printing - limit the use of colour and keep the label simple and sophisticated.
Emberlace Candle Co. is our company name. Emberlace being the predominant name and candle co. written small underneath right justified.
Die cut labels might look better than a rectangle.
Dimensions should be 90mm Wide x 90mm High
The final design should communicate a professional and quality product. But stay modern and professional. Clean, elegant and sophisticated.
Can use wording such as: Hand Poured, Premium Soy Wax, All Natural, Up cycled
Have a look at the attached image for the look and feel we are going for.
Updates
Designers are having a little bit of trouble interpreting the brief into a viable design. To assist perhaps you can look at WINE LABELS on google images. Design your label around an existing style wine label to give the canld ethe feel of being a bottle of wine. Get creative! :)
Reason: We require more designs. We havnt quite got what were looking for.
Please see brief.

```html
<!DOCTYPE html>
<html lang="en">
<head>
<meta charset="utf-8">
<title>Emberlace Candle Co. – Soy Candle Label</title>
<link href="https://fonts.googleapis.com/css2?family=Cormorant+Garamond:wght@500&family=Oswald:wght@500&display=swap" rel="stylesheet">
<style>
  :root {
    --paper: #fefbe2;
    --bronze: #b86d2c;
    --ring: #dcab85;
    --sage: #b6c496;
  }
  html, body {
    margin: 0;
    padding: 0;
    width: 1200px;
    height: 1200px;
    overflow: hidden;
    background: var(--paper);
  }
  .label {
    position: relative;
    width: 1200px;
    height: 1200px;
    background: var(--paper);
    font-family: "Cormorant Garamond", Georgia, serif;
    font-weight: 500;
    color: var(--bronze);
    overflow: hidden;
  }
  .top-band {
    position: absolute;
    left: 0; top: 0;
    width: 100%;
    height: 14px;
    background: var(--bronze);
  }
  .claims {
    position: absolute;
    left: 70px;
    top: 284px;
    margin: 0;
    font-size: 31px;
    letter-spacing: 0.5px;
    text-transform: uppercase;
    white-space: nowrap;
  }
  .claims .divider { margin: 0 16px; }
  .rule-lines {
    position: absolute;
    left: 0; top: 338px;
  }
  .scent-stamp {
    position: absolute;
    left: 0; top: 0;
  }
  .scent-caption {
    position: absolute;
    left: 832px;
    top: 364px;
    transform: translate(-50%, -50%) rotate(-90deg);
    font-size: 26px;
    letter-spacing: 1px;
    text-transform: uppercase;
  }
  .scent-name {
    position: absolute;
    left: 1010px;
    top: 364px;
    transform: translate(-50%, -50%);
    margin: 0;
    font-family: "Oswald", "Arial Narrow", sans-serif;
    font-weight: 500;
    font-size: 66px;
    line-height: 0.98;
    text-align: center;
    color: var(--sage);
    text-transform: uppercase;
  }
  .brand {
    position: absolute;
    left: 0;
    top: 600px;
    width: 1140px;
    margin: 0;
    text-align: right;
    font-weight: 500;
  }
  .brand-name {
    display: block;
    font-size: 268px;
    line-height: 1;
    letter-spacing: -2px;
    white-space: nowrap;
  }
  .brand-sub {
    display: block;
    margin-top: 8px;
    font-size: 48px;
    letter-spacing: 1px;
    text-transform: uppercase;
  }
  .footer-note {
    position: absolute;
    top: 1120px;
    margin: 0;
    font-size: 28px;
    text-transform: uppercase;
    white-space: nowrap;
    font-variant-numeric: oldstyle-nums;
  }
  .origin { left: 68px; }
  .net-weight { right: 69px; }
</style>
</head>
<body>
  <main class="label">
    <div class="top-band"></div>

    <p class="claims">Hand Poured<span class="divider">|</span>All Natural Soy</p>

    <svg class="rule-lines" width="694" height="16" viewBox="0 0 694 16" aria-hidden="true">
      <line x1="0" y1="4" x2="692" y2="4" stroke="var(--bronze)" stroke-width="2.2"/>
      <line x1="0" y1="11" x2="692" y2="11" stroke="var(--bronze)" stroke-width="2.2"/>
    </svg>

    <svg class="scent-stamp" width="1200" height="1200" viewBox="0 0 1200 1200" aria-hidden="true">
      <circle cx="1010" cy="364" r="149" fill="none" stroke="var(--ring)" stroke-width="3.5"/>
    </svg>
    <span class="scent-caption">Scent</span>
    <p class="scent-name">Scent<br>Name</p>

    <h1 class="brand">
      <span class="brand-name">Emberlace</span>
      <span class="brand-sub">Candle Co.</span>
    </h1>

    <p class="footer-note origin">Product of Australia</p>
    <p class="footer-note net-weight">320 gm. Premium Soy Wax</p>
  </main>
</body>
</html>
```